SkyvornQ Business Cards and Stationary Design

Need a design for our business cards and stationary. I want to carry on the theme of the logo. I want the business cards to have a design on the back. I would like the business cards and the stationary to carry the same theme, design scheme, and branding

Target Market(s)

Airlines and Maintenance Facilities

Industry/Entity Type

Aviation

Contact Information for Business Card

Name
Position Title
Address: 4827 Trellis Hollow Road, Fort Pierce, Florida, 34951
Office Number
Mobile Number
Email
Website

Font styles to use
Serif
Sans Serif

Colors

Designer to choose colors to be used in the design.

```html
<!DOCTYPE html>
<html lang="en">
<head>
<meta charset="utf-8">
<title>SkyvornQ Business Card</title>
<link rel="stylesheet" href="https://fonts.googleapis.com/css2?family=Work+Sans:wght@400;500;600;700&display=swap">
<style>
  :root {
    --navy: #14294f;
    --navy-text: #1a2b52;
    --sky: #2a9fd8;
    --white: #ffffff;
    --grey-text: #555b66;
    --backdrop: #e9e9ea;
  }
  * { box-sizing: border-box; margin: 0; padding: 0; }
  html, body { width: 1200px; height: 960px; overflow: hidden; }
  body {
    background: var(--backdrop);
    font-family: "Work Sans", Arial, sans-serif;
    position: relative;
  }
  .card {
    position: absolute;
    left: 270px;
    width: 664px;
    height: 380px;
    box-shadow: 0 3px 10px rgba(0,0,0,0.18);
    overflow: hidden;
  }
  .card--front { top: 72px; background: var(--navy); color: var(--white); }
  .card--back { top: 509px; background: var(--white); }

  /* Front */
  .front-mark {
    position: absolute;
    left: 50%; top: 78px;
    width: 130px; height: 130px;
    margin-left: -63px;
    border: 10px solid var(--white);
    border-radius: 50%;
  }
  .front-name {
    position: absolute;
    left: 0; right: 0; top: 228px;
    text-align: center;
    font-weight: 600;
    font-size: 44px;
    letter-spacing: 5px;
    text-transform: uppercase;
  }
  .front-web {
    position: absolute;
    left: 0; right: 0; top: 327px;
    text-align: center;
    font-weight: 600;
    font-size: 16px;
  }

  /* Back */
  .back-mark {
    position: absolute;
    left: 106px; top: 36px;
    width: 78px; height: 78px;
    border: 6px solid var(--navy);
    border-radius: 50%;
  }
  .back-name {
    position: absolute;
    left: 27px; top: 126px;
    font-weight: 600;
    font-size: 27px;
    letter-spacing: 3px;
    color: var(--navy-text);
    text-transform: uppercase;
  }
  .person {
    position: absolute;
    right: 26px; top: 182px;
    text-align: right;
    color: var(--navy-text);
  }
  .person__name { font-size: 28px; font-weight: 500; letter-spacing: 0.5px; line-height: 36px; }
  .person__title { font-size: 16px; letter-spacing: 1px; color: #2b3346; line-height: 22px; }
  .divider {
    position: absolute;
    left: 27px; right: 26px; top: 246px;
    height: 2px; background: var(--navy);
  }
  .contact {
    position: absolute;
    top: 282px;
    font-size: 15px;
    line-height: 20.5px;
    color: var(--grey-text);
  }
  .contact--left { left: 27px; }
  .contact--right { right: 26px; top: 302px; text-align: left; }
  .contact__label { color: var(--navy-text); font-weight: 500; }
  .footer-band { position: absolute; left: 0; bottom: 0; width: 664px; height: 10px; }
</style>
</head>
<body>
  <section class="card card--front" aria-label="Business card front">
    <div class="front-mark"></div>
    <div class="front-name">SkyvornQ</div>
    <div class="front-web">www.skyvornq.com</div>
  </section>

  <section class="card card--back" aria-label="Business card back">
    <div class="back-mark"></div>
    <div class="back-name">SkyvornQ</div>

    <div class="person">
      <div class="person__name">Marcus Delane</div>
      <div class="person__title">Director</div>
    </div>
    <div class="divider"></div>

    <div class="contact contact--left">
      <div><span class="contact__label">Mobile:</span> 0427 516 908</div>
      <div><span class="contact__label">Phone:</span> 500-718-0396</div>
      <div><span class="contact__label">Email:</span> md@skyvornq.com</div>
    </div>
    <div class="contact contact--right">
      <div><span class="contact__label">Address:</span> 4827 Trellis Hollow Road</div>
      <div>Fort Pierce, Florida, 34951</div>
    </div>

    <svg class="footer-band" viewBox="0 0 664 10" preserveAspectRatio="none" aria-hidden="true">
      <polygon points="0,0 320,0 311,10 0,10" fill="var(--sky)"/>
      <polygon points="338,0 664,0 664,10 328,10" fill="var(--navy)"/>
    </svg>
  </section>
</body>
</html>
```